Direct to Consumer extended service contract business with a new disruptive business model needs a

We need a customized wordpress design for a company called 'Bright Harbor Assurance'.
We provide an innovative and unique service contract protection program direct to consumers. This program provides monthly coverage for all electronics purchased in the last 4 years and all electronics the consumer purchases in the future for a low monthly fee. The overall design should communicate a sense of legitimacy, ethics, and superior customer service and support (in an industry that has a huge PR issue to overcome).
Electronics is the first product group, other product groups with different price points to launch in the future..

Target Market(s)

All purchasers of electronic goods...all demographics

Industry/Entity Type

Electronics

Font styles to use
Sans Serif

Requirements
Must have
• Customer Testimonials
Industry News
Customer ratings
Blog posts
Call to action messaging
Like the functional elements and design of quillmesa.example (need to be better)
Nice to have
• Like to see video testimonials
Social network "whats trending related to electronics or service contract industry"
Easy way to register products for warranty

```html
<!DOCTYPE html>
<html lang="en">
<head>
<meta charset="utf-8">
<title>Bright Harbor Assurance</title>
<link rel="stylesheet" href="https://fonts.googleapis.com/css2?family=Ubuntu:wght@400;500&family=Lato:wght@400;700&display=swap">
<style>
:root{
  --green:#0f7a2c;
  --green-dark:#0b6a25;
  --text:#5a5a5a;
  --dark:#2a2a2a;
  --line:#e8e8e8;
  --white:#ffffff;
  --star-blue:#1e7fd8;
  --star-red:#a8473d;
}
*{margin:0;padding:0;box-sizing:border-box}
html,body{width:726px;height:1200px;overflow:hidden;background:var(--white)}
body{position:relative;font-family:'Lato',sans-serif;color:var(--text)}
.abs{position:absolute}
.site-header{position:absolute;left:0;top:0;width:726px;height:48px;background:var(--white)}
.brand{position:absolute;left:78px;top:14px;font-family:'Lato',sans-serif;font-weight:700;font-size:14px;color:var(--green);display:flex;align-items:center;gap:6px}
.brand-mark{width:10px;height:10px;background:var(--green)}
.main-nav{position:absolute;top:16px;left:286px;font-family:'Ubuntu',sans-serif;font-size:10px;color:#666}
.main-nav span{position:absolute;white-space:nowrap}
.main-nav .active{color:var(--dark)}
.main-nav .active::after{content:"";position:absolute;left:0;right:0;top:15px;height:3px;background:var(--green)}
.hero{position:absolute;left:0;top:49px;width:726px;height:219px;background:linear-gradient(100deg,#c9cdd2 0%,#dfe2e4 35%,#a9b0b8 60%,#3b4048 100%)}
.hero-title{position:absolute;left:79px;top:13px;font-family:'Ubuntu',sans-serif;font-weight:400;font-size:24px;line-height:31.5px;color:var(--white);white-space:nowrap}
.hero-arrow{position:absolute;top:93px}
h2{position:absolute;font-family:'Ubuntu',sans-serif;font-weight:400;font-size:21px;color:var(--green);white-space:nowrap}
.body-text{position:absolute;font-size:8.4px;line-height:15.5px;color:var(--text)}
.photo{position:absolute}
.date-tag{position:absolute;left:0;bottom:6px;background:rgba(40,40,40,.8);color:#fff;font-size:9px;padding:5px 7px}
.card-title{position:absolute;font-family:'Ubuntu',sans-serif;font-size:14.5px;color:var(--dark);white-space:nowrap}
.read-more{position:absolute;font-size:8.6px;color:var(--green)}
.date-box{position:absolute;width:60px;height:60px;background:var(--green);color:#fff;font-family:'Ubuntu',sans-serif;font-size:17px;line-height:24px;text-align:center;padding-top:6px}
.rating-label{position:absolute;font-size:8.6px;color:var(--dark);text-align:center;width:129px}
.stars{position:absolute}
.social-item .avatar{position:absolute;border:1px solid #ddd;box-shadow:1px 1px 3px rgba(0,0,0,.2)}
.social-text{position:absolute;font-size:8.2px;line-height:15.5px;color:var(--text);width:200px}
.social-text b{font-weight:400;color:var(--green)}
.view-all{position:absolute;font-size:8.6px;color:var(--green);text-decoration:underline}
.cta-text{position:absolute;left:546px;top:950px;font-family:'Ubuntu',sans-serif;font-size:12px;line-height:20px;color:var(--dark)}
.signup{position:absolute;left:421px;top:1050px;width:125px;height:28px;background:var(--green);color:#fff;font-family:'Ubuntu',sans-serif;font-size:14px;line-height:28px;text-align:center}
.site-footer{position:absolute;left:0;top:1122px;width:726px;height:78px;background:var(--green-dark)}
.copyright{position:absolute;top:16px;width:100%;text-align:center;color:#fff;font-size:8.6px}
.social-icons{position:absolute;left:302px;top:42px}
</style>
</head>
<body>

<header class="site-header">
  <div class="brand"><span class="brand-mark"></span>Bright Harbor Assurance</div>
  <nav class="main-nav">
    <span class="active" style="left:0">Home</span>
    <span style="left:51px">Plans</span>
    <span style="left:100px">Benefits</span>
    <span style="left:162px">FAQ's</span>
    <span style="left:213px">About Us</span>
    <span style="left:279px">Login</span>
    <span style="left:328px">Support</span>
  </nav>
</header>

<section class="hero" role="img" aria-label="Photo of hands holding a smartphone over paperwork">
  <h1 class="hero-title">The days of buying<br>expensive In-store<br>service plans<br>are over!</h1>
  <svg class="hero-arrow" style="left:8px" width="20" height="20" viewBox="0 0 20 20"><circle cx="10" cy="10" r="9" fill="rgba(255,255,255,.35)" stroke="#fff" stroke-width="1.5"/><path d="M12 5 L7 10 L12 15" fill="none" stroke="#fff" stroke-width="2"/></svg>
  <svg class="hero-arrow" style="left:699px" width="20" height="20" viewBox="0 0 20 20"><circle cx="10" cy="10" r="9" fill="rgba(0,0,0,.3)" stroke="#fff" stroke-width="1.5"/><path d="M8 5 L13 10 L8 15" fill="none" stroke="#fff" stroke-width="2"/></svg>
</section>

<section class="who-we-are">
  <h2 style="left:78px;top:280px">Who We Are</h2>
  <p class="body-text" style="left:78px;top:310px;width:466px">The days of costly, store-bought extended warranties are coming to an end. Bright Harbor Assurance is revolutionizing the extended service and repair industry! Traditional service plans purchased at big box electronic stores or online require you to pay large upfront premiums for each consumer electronics device protected. With Bright Harbor Assurance, you are able to cover all of your eligible electronic devices.</p>
  <div class="photo" style="left:550px;top:284px;width:96px;height:90px;border-radius:6px;background:radial-gradient(circle at 50% 55%,#cfe4ef,#ffffff 75%)" role="img" aria-label="Illustration of a support agent with a laptop and a protection shield"></div>
</section>

<section class="industry-news">
  <h2 style="left:78px;top:391px">Industry News</h2>
  <div class="photo" style="left:78px;top:426px;width:145px;height:103px;background:linear-gradient(110deg,#7e95b0,#c9ccd0 50%,#3f4550)" role="img" aria-label="Photo of a businessman using a phone">
    <span class="date-tag">March, 2014</span></div>
  <div class="photo" style="left:238px;top:426px;width:145px;height:103px;background:linear-gradient(180deg,#d8d8d8,#8a8a8e 55%,#2e3340)" role="img" aria-label="Photo of a smiling business team">
    <span class="date-tag">April, 2014</span></div>
  <div class="card-title" style="left:78px;top:540px">Lorem ipsum dolor</div>
  <p class="body-text" style="left:78px;top:564px;width:140px">Lorem ipsum dolor sit amet, ei ullum laudem sed, has et postea.</p>
  <a class="read-more" style="left:78px;top:601px">Read More</a>
  <div class="card-title" style="left:237px;top:540px">Lorem ipsum dolor</div>
  <p class="body-text" style="left:237px;top:564px;width:140px">Lorem ipsum dolor sit amet, ei ullum laudem sed, has et postea.</p>
  <a class="read-more" style="left:237px;top:601px">Read More</a>
</section>

<section class="blog-posts">
  <h2 style="left:419px;top:392px">Blog posts</h2>
  <p class="body-text" style="left:421px;top:422px;width:220px">Te cum veritus deleniti apeirian, illum omnesque sig-niferumque nam ad.</p>
  <div class="date-box" style="left:421px;top:470px">Mar<br>22</div>
  <div class="card-title" style="left:495px;top:467px;font-size:14px">Assum alterum</div>
  <p class="body-text" style="left:495px;top:489px;width:160px">Ad consul sapientem sadipscing ius, id insolens disputationi mediocritatem.</p>
  <a class="read-more" style="left:495px;top:523px">Read More</a>
  <div class="date-box" style="left:421px;top:549px">Apr<br>02</div>
  <div class="card-title" style="left:495px;top:546px;font-size:14px">Ad consul sapientem</div>
  <p class="body-text" style="left:495px;top:567px;width:160px">Ad consul sapientem sadipscing ius, id insolens disputationi mediocritatem.</p>
  <a class="read-more" style="left:495px;top:601px">Read More</a>
</section>

<section class="customer-ratings">
  <h2 style="left:78px;top:637px">Customer ratings</h2>
  <div class="photo" style="left:79px;top:674px;width:129px;height:74px;background:linear-gradient(180deg,#6fa6d6,#c7dbe8 55%,#9aa86a)" role="img" aria-label="Photo of a hand holding a phone against the sky"></div>
  <div class="photo" style="left:245px;top:674px;width:129px;height:74px;background:linear-gradient(135deg,#5a3a2c,#3a2e2c 60%,#2a2d38)" role="img" aria-label="Photo of a person typing on a laptop"></div>
  <div class="rating-label" style="left:79px;top:761px">Pinecone app hub</div>
  <div class="rating-label" style="left:245px;top:761px">Riverstall</div>
  <svg class="stars" style="left:113px;top:784px" width="57" height="9" viewBox="0 0 57 9"><g fill="var(--star-blue)"><polygon id="s" points="4.5,0 5.6,3.2 9,3.3 6.3,5.3 7.3,8.6 4.5,6.6 1.7,8.6 2.7,5.3 0,3.3 3.4,3.2"/><use href="#s" x="12"/><use href="#s" x="24"/><use href="#s" x="36"/><use href="#s" x="48"/></g></svg>
  <svg class="stars" style="left:280px;top:784px" width="57" height="9" viewBox="0 0 57 9"><g fill="var(--star-red)"><use href="#s"/><use href="#s" x="12"/><use href="#s" x="24"/><use href="#s" x="36"/><use href="#s" x="48"/></g></svg>
</section>

<section class="social-network">
  <h2 style="left:420px;top:637px">Social network</h2>
  <div class="social-item">
    <div class="avatar" style="left:421px;top:674px;width:45px;height:42px;background:linear-gradient(180deg,#e8e6e4,#a2846e)" role="img" aria-label="Profile photo of a customer"></div>
    <p class="social-text" style="left:479px;top:670px"><b>@ bright harbor</b> just received the <b>#<br>customer</b> sapientem sadipscing ius, id.<br>7 hours ago</p>
  </div>
  <div class="social-item">
    <div class="avatar" style="left:421px;top:728px;width:45px;height:42px;background:linear-gradient(180deg,#f0f0f0,#4a4a50)" role="img" aria-label="Profile photo of a customer"></div>
    <p class="social-text" style="left:479px;top:724px"><b>@ bright harbor</b> just received the <b>#<br>customer</b> sapientem sadipscing ius, id.<br>1 day 2 hours ago</p>
  </div>
  <a class="view-all" style="left:421px;top:781px">View all</a>
</section>

<section class="testimonials">
  <h2 style="left:78px;top:820px">Customer Testimonials</h2>
  <div class="photo" style="left:79px;top:858px;width:149px;height:110px;background:linear-gradient(120deg,#c9822e,#8a5a3a 60%,#3a4a6a)" role="img" aria-label="Video testimonial still of a smiling man"></div>
  <div class="photo" style="left:228px;top:858px;width:149px;height:110px;background:linear-gradient(180deg,#eef0f2,#c4d0da)" role="img" aria-label="Video testimonial still of a man at a laptop"></div>
  <div class="photo" style="left:79px;top:968px;width:149px;height:110px;background:linear-gradient(160deg,#bfc3c8,#4a5a7a 70%)" role="img" aria-label="Video testimonial still of a man with a tablet on steps"></div>
  <div class="photo" style="left:228px;top:968px;width:149px;height:110px;background:linear-gradient(90deg,#d6dbe0,#8c96a2 50%,#e6e9ec)" role="img" aria-label="Video testimonial still of a businessman in an office"></div>
  <svg class="abs" style="left:214px;top:956px" width="27" height="27" viewBox="0 0 27 27"><circle cx="13.5" cy="13.5" r="12" fill="#d9261c" stroke="#fff" stroke-width="2"/><polygon points="10,8 19,13.5 10,19" fill="#fff"/></svg>
</section>

<section class="get-protection">
  <h2 style="left:420px;top:821px">Get Bright Harbor protection</h2>
  <p class="body-text" style="left:421px;top:854px;width:230px">Every Bright Harbor Electronics Service Plan is fully insured, and value depreciation is a thing of the past. If a protected product is beyond repair and a replacement product is not available, Bright Harbor will cover the cost of the <span style="color:var(--green)">ORIGINAL PURCHASE PRICE.</span></p>
  <div class="photo" style="left:421px;top:946px;width:112px;height:86px;background:linear-gradient(160deg,#4a4e56,#6c7280)" role="img" aria-label="Illustration announcing that every electronics service plan is fully insured"></div>
  <p class="cta-text">Get Your Bright Harbor<br>protection<br>Today!</p>
  <a class="signup">Sign up now !</a>
</section>

<footer class="site-footer">
  <p class="copyright">Copyright @ 2014 brightharbor.example.All rights reserved.</p>
  <svg class="social-icons" width="72" height="20" viewBox="0 0 72 20"><g fill="none" stroke="#fff" stroke-width="1.2"><circle cx="10" cy="10" r="8.5"/><circle cx="36" cy="10" r="8.5"/><circle cx="61" cy="10" r="8.5"/></g></svg>
</footer>

</body>
</html>
```